Shine Fox Auto Care Business Card

2 side business card design for an auto detailing business

Target Market(s)

Auto detailing

Contact Information for Business Card

Things included

The business name “Shine Fox Auto Care”
Mark Dunrow
(403)271-6094
Kelmont, Sk

Services offered - complete interior& exterior detail
- paint correction & protection
- ceramic coating
- trim restore
- auto carpet & seat cleaning

Requirements
Must have
• Colours that are in my logo

Services offered

My name Mark Dunrow
403-271-6094
Kelmont, Sk

Not too sure in what order for these ?
Website. Shinefoxautocare.com
Instagram Shinefoxautocare
Email. Shinefoxautoac@mailvento.com

```html
<!DOCTYPE html>
<html lang="en">
<head>
<meta charset="utf-8">
<title>Shine Fox Auto Care – Business Card</title>
<link href="https://fonts.googleapis.com/css2?family=Montserrat:wght@400;500;700&display=swap" rel="stylesheet">
<style>
  :root {
    --bg: #8a8a8a;
    --card-light: #ffffff;
    --card-dark: #1f1f1f;
    --red: #8b0000;
    --ink: #111111;
    --grey: #555555;
    --white: #ffffff;
  }
  * { margin: 0; padding: 0; box-sizing: border-box; }
  html, body { width: 1200px; height: 1200px; overflow: hidden; }
  body {
    background: var(--bg);
    font-family: 'Montserrat', sans-serif;
    position: relative;
  }
  .card {
    position: absolute;
    left: 200px;
    width: 800px;
    height: 456px;
    border-radius: 26px;
  }
  .card-front { top: 88px; background: var(--card-light); }
  .card-back { top: 656px; background: var(--card-dark); }

  /* front */
  .brand {
    position: absolute;
    left: 104px;
    top: 148px;
    width: 262px;
    text-align: center;
  }
  .brand-ring {
    width: 90px; height: 90px;
    margin: 0 auto 14px;
    border: 9px solid var(--red);
    border-radius: 50%;
  }
  .brand-name {
    color: var(--ink);
    font-weight: 500;
    font-size: 27px;
    line-height: 1.1;
    letter-spacing: 1px;
    text-transform: uppercase;
  }
  .divider {
    position: absolute;
    left: 385px; top: 147px;
    width: 1.5px; height: 158px;
    background: var(--ink);
  }
  .contact {
    position: absolute;
    left: 411px; top: 138px;
  }
  .contact-name {
    color: var(--red);
    font-weight: 500;
    font-size: 27px;
    letter-spacing: 0.5px;
    text-transform: uppercase;
  }
  .contact-location {
    color: var(--grey);
    font-size: 18px;
    margin: 12px 0 14px;
  }
  .contact-list { list-style: none; }
  .contact-list li {
    display: flex; align-items: center;
    color: var(--grey);
    font-size: 18px;
    line-height: 22.5px;
  }
  .contact-list svg { width: 16px; height: 16px; margin-right: 10px; flex: none; }

  /* back */
  .mark {
    position: absolute;
    left: 312px; top: 106px;
    width: 176px; height: 176px;
    border: 16px solid var(--red);
    border-radius: 50%;
    display: flex; align-items: center; justify-content: center;
    text-align: center;
    color: var(--red);
    font-weight: 700;
    font-size: 20px;
    line-height: 1.15;
    text-transform: uppercase;
  }
  .services {
    position: absolute;
    left: 0; right: 0; top: 324px;
    text-align: center;
  }
  .services-title {
    color: var(--red);
    font-weight: 700;
    font-size: 18px;
    text-transform: uppercase;
    margin-bottom: 10px;
  }
  .services-line {
    color: var(--white);
    font-size: 19px;
    line-height: 24px;
  }
  .dot {
    display: inline-block;
    width: 6px; height: 6px;
    border-radius: 50%;
    background: var(--red);
    margin: 0 9px;
    vertical-align: middle;
  }
</style>
</head>
<body>
  <section class="card card-front">
    <div class="brand">
      <div class="brand-ring"></div>
      <div class="brand-name">Shine Fox<br>Auto Care</div>
    </div>
    <div class="divider"></div>
    <div class="contact">
      <h1 class="contact-name">Mark Dunrow</h1>
      <p class="contact-location">Kelmont, Sk</p>
      <ul class="contact-list">
        <li>
          <svg viewBox="0 0 16 16" aria-hidden="true"><path fill="#8b0000" d="M3.5 1.5l2.5 0 1 3.5-1.6 1.2c.8 1.8 2.2 3.2 4 4l1.2-1.6 3.4 1v2.5c0 .8-.7 1.4-1.5 1.4C6.7 13.2 2.8 9.3 2.1 3c0-.8.6-1.5 1.4-1.5z"/></svg>
          (403)271-6094
        </li>
        <li>
          <svg viewBox="0 0 16 16" aria-hidden="true"><rect x="1.5" y="3.5" width="13" height="9" fill="#8b0000"/><path d="M2 4l6 4.5L14 4" stroke="#fff" stroke-width="1.2" fill="none"/></svg>
          Shinefoxautoac@mailvento.com
        </li>
        <li>
          <svg viewBox="0 0 16 16" aria-hidden="true"><circle cx="8" cy="8" r="6.5" fill="#8b0000"/><path d="M1.5 8h13M8 1.5c-3 3.5-3 9.5 0 13M8 1.5c3 3.5 3 9.5 0 13" stroke="#fff" stroke-width="1" fill="none"/></svg>
          www.Shinefoxautocare.com
        </li>
        <li>
          <svg viewBox="0 0 16 16" aria-hidden="true"><circle cx="8" cy="8" r="6" fill="none" stroke="#8b0000" stroke-width="2"/></svg>
          ShineFoxAutoCare
        </li>
      </ul>
    </div>
  </section>

  <section class="card card-back">
    <div class="mark">Shine<br>Fox</div>
    <div class="services">
      <h2 class="services-title">Complete Interior &amp; Exterior Detail</h2>
      <p class="services-line">Paint correction &amp; Protection<span class="dot"></span>Ceramic coating</p>
      <p class="services-line">Trim restore<span class="dot"></span>Auto carpet &amp; Seat cleaning</p>
    </div>
  </section>
</body>
</html>
```